Harborline Auto LLC

Car Dealer Customer Service
Address: 2874 Cresthaven Road, Shelbyville, TN 37162
web: www.harborlineautoxq.net
email: harborlineautoxq@mailnest.example
Phone: (931) 555-0148
Phone: (629) 555-0173

```html
<!DOCTYPE html>
<html lang="en">
<head>
<meta charset="utf-8">
<title>Harborline Auto – Business Card</title>
<link rel="stylesheet" href="https://fonts.googleapis.com/css2?family=Poppins:wght@400;600;700&display=swap">
<style>
  :root{
    --bg:#2b2b2b;
    --card:#efefef;
    --card-edge:#f6f6f6;
    --blue:#1f76a8;
    --blue-dark:#1a6690;
    --gold:#d9a23a;
    --ink:#2a2a2a;
  }
  *{box-sizing:border-box;margin:0;padding:0}
  html,body{width:1200px;height:1138px;overflow:hidden;background:var(--bg);font-family:"Poppins",sans-serif}
  .card{position:absolute;width:620px;height:375px;border-radius:16px;overflow:hidden;
    background:linear-gradient(135deg,var(--card-edge),var(--card));}
  .card--front{left:274px;top:186px}
  .card--back{left:276px;top:608px}

  .brand{position:absolute;display:flex;align-items:center;gap:10px;
    font-weight:700;color:var(--blue);letter-spacing:.5px;white-space:nowrap}
  .brand__dot{width:18px;height:18px;border-radius:50%;background:var(--gold);flex:none}
  .card--front .brand{left:0;right:0;justify-content:center;top:216px;font-size:30px}
  .card--back .brand{left:26px;width:250px;justify-content:center;top:232px;font-size:24px}

  .front__web{position:absolute;left:0;right:0;top:320px;display:flex;justify-content:center;align-items:center;gap:22px;
    font-size:15px;color:var(--ink)}
  .front__web::before,.front__web::after{content:"";width:54px;height:2px;background:var(--gold)}
  .front__bands{position:absolute;left:0;right:0;bottom:0;height:18px;display:flex}
  .front__bands span:first-child{flex:1;background:var(--blue)}
  .front__bands span:last-child{flex:1;background:var(--gold)}

  .contact{position:absolute;left:322px;top:62px;color:var(--ink)}
  .contact__name{font-size:24px;font-weight:700;color:var(--blue-dark);line-height:1.2}
  .contact__title{font-size:15px;line-height:1.3}
  .contact__address{margin-top:22px;font-size:15px;line-height:1.45}
  .contact__list{list-style:none;margin-top:12px}
  .contact__list li{display:flex;align-items:center;gap:10px;font-size:15px;line-height:22px}
  .contact__list li.is-phone{font-weight:600;color:var(--blue-dark);font-size:16px}
  .contact__list li.is-email{font-size:14px}
  .contact__list svg{width:14px;height:14px;flex:none;fill:var(--gold)}

  .back__stripe{position:absolute;left:0;right:0;bottom:0;height:15px;background:var(--gold)}
  .back__tab{position:absolute;right:0;bottom:0;width:355px;height:46px;background:var(--blue);
    clip-path:polygon(18px 0,100% 0,100% 100%,0 100%)}
  .back__tab-label{position:absolute;left:322px;bottom:13px;font-size:16px;font-weight:700;color:#fff;letter-spacing:.3px}
</style>
</head>
<body>
  <section class="card card--front">
    <div class="brand"><span class="brand__dot"></span>Harborline Auto</div>
    <p class="front__web">www.harborlineautoxq.net</p>
    <div class="front__bands"><span></span><span></span></div>
  </section>

  <section class="card card--back">
    <div class="brand"><span class="brand__dot"></span>Harborline Auto</div>
    <div class="contact">
      <h1 class="contact__name">Daniel Rowe</h1>
      <p class="contact__title">Managing Director</p>
      <p class="contact__address">2874 Cresthaven Road,<br>Shelbyville, TN 37162</p>
      <ul class="contact__list">
        <li class="is-phone"><svg viewBox="0 0 24 24"><path d="M6.6 10.8a15 15 0 0 0 6.6 6.6l2.2-2.2c.3-.3.7-.4 1-.2 1.1.4 2.3.6 3.6.6.6 0 1 .4 1 1V20c0 .6-.4 1-1 1A17 17 0 0 1 3 4c0-.6.4-1 1-1h3.5c.6 0 1 .4 1 1 0 1.3.2 2.5.6 3.6.1.3 0 .7-.2 1z"/></svg>(931) 555-0148</li>
        <li class="is-phone"><svg viewBox="0 0 24 24"><path d="M6.6 10.8a15 15 0 0 0 6.6 6.6l2.2-2.2c.3-.3.7-.4 1-.2 1.1.4 2.3.6 3.6.6.6 0 1 .4 1 1V20c0 .6-.4 1-1 1A17 17 0 0 1 3 4c0-.6.4-1 1-1h3.5c.6 0 1 .4 1 1 0 1.3.2 2.5.6 3.6.1.3 0 .7-.2 1z"/></svg>(629) 555-0173</li>
        <li><svg viewBox="0 0 24 24"><path d="M2 5h20v14H2zm2 2v.5l8 5 8-5V7zm0 2.8V17h16V9.8l-8 5z"/></svg>www.harborlineautoxq.net</li>
        <li class="is-email"><svg viewBox="0 0 24 24"><path d="M12 2a10 10 0 1 0 0 20 10 10 0 0 0 0-20zm6.9 9h-3a15 15 0 0 0-1.3-5.6A8 8 0 0 1 18.9 11zM12 4c.9 1.2 1.8 3.6 1.9 7h-3.8c.1-3.4 1-5.8 1.9-7zM9.4 5.4A15 15 0 0 0 8.1 11h-3a8 8 0 0 1 4.3-5.6zM5.1 13h3a15 15 0 0 0 1.3 5.6A8 8 0 0 1 5.1 13zM12 20c-.9-1.2-1.8-3.6-1.9-7h3.8c-.1 3.4-1 5.8-1.9 7zm2.6-1.4a15 15 0 0 0 1.3-5.6h3a8 8 0 0 1-4.3 5.6z"/></svg>harborlineautoxq@mailnest.example</li>
      </ul>
    </div>
    <div class="back__stripe"></div>
    <div class="back__tab"></div>
    <p class="back__tab-label">HARBORLINE AUTO LLC</p>
  </section>
</body>
</html>
```